Tiny educational app company needs a big new website

We need to re-do our ageing website (www.quietpebbleapps.com). Our site is mostly visited by primary school teachers or parents of primary school kids. 90% of our apps are tablets only so an tablets optimised design would be helpful.

We would like the monkey to remain part of the design if possible. I'm not sure if the orange/ blue/ white should stay - if you have a good design and a strong opinion it should go we could be open to change.

Target Market(s)

Teachers, parents

Industry/Entity Type

Education

Number of Pages Required

3 page

Font styles to use
Sans Serif

Colors

Designer to choose colors to be used in the design.

Requirements
Must have
• Needs to show all of our apps (somehow... open to a new way of achieving this)

```html
<!DOCTYPE html>
<html lang="en">
<head>
<meta charset="utf-8">
<title>Quiet Pebble Apps</title>
<link href="https://fonts.googleapis.com/css2?family=Roboto:wght@400;500;700&display=swap" rel="stylesheet">
<style>
:root{
  --header-blue:#1d7fcf;
  --accent-orange:#d2531a;
  --tile-navy:#1d3b5c;
  --footer-navy:#244f72;
  --monkey-orange:#e2691f;
  --wood:#b98a55;
  --wood-light:#d8b282;
  --wood-dark:#a9794a;
  --ink:#1a1a1a;
  --white:#ffffff;
  --line:#d8d8d8;
}
*{box-sizing:border-box;margin:0;padding:0}
html,body{width:1200px;height:2276px;overflow:hidden}
body{position:relative;background:var(--white);font-family:'Roboto',Arial,sans-serif;color:var(--ink)}
a{color:inherit;text-decoration:none}

.site-header{position:absolute;left:0;top:0;width:1200px;height:93px;background:var(--header-blue)}
.brand{position:absolute;left:54px;top:18px;display:flex;align-items:center;gap:18px;color:var(--white);font-weight:700;font-size:33px}
.brand-dot{width:56px;height:56px;border-radius:50%;background:var(--monkey-orange)}
.menu-toggle{position:absolute;left:853px;top:30px}
.social-dots{position:absolute;left:913px;top:20px;display:flex;gap:9px}
.social-dot{width:53px;height:53px;border-radius:50%;border:3px solid var(--white)}
.social-dot.a{background:#2c4b8e}.social-dot.b{background:#c8232c}.social-dot.c{background:#e62117}.social-dot.d{background:#1da1f2}

.hero{position:absolute;left:53px;top:179px;width:1095px;height:435px;border:1px solid var(--line);background:var(--white)}
.hero-image{position:absolute;left:4px;top:4px;width:644px;height:425px;
  background:
    radial-gradient(ellipse 120px 140px at 530px 110px,rgba(240,200,80,.55),rgba(240,200,80,0) 100%),
    radial-gradient(ellipse 200px 150px at 140px 330px,rgba(235,235,235,.45),rgba(235,235,235,0) 100%),
    radial-gradient(ellipse 170px 110px at 340px 300px,rgba(230,230,230,.35),rgba(230,230,230,0) 100%),
    radial-gradient(ellipse 140px 70px at 150px 50px,rgba(245,245,245,.4),rgba(245,245,245,0) 100%),
    linear-gradient(100deg,var(--wood-light),var(--wood) 55%,var(--wood-dark))}
.hero-arrow{position:absolute;top:192px;width:44px;height:52px;background:rgba(0,0,0,.45);display:flex;align-items:center;justify-content:center}
.hero-arrow.prev{left:4px}.hero-arrow.next{left:604px}
.hero-panel{position:absolute;left:654px;top:0;width:440px;height:434px;background:var(--accent-orange);color:var(--white);padding:44px 0 0 44px}
.hero-title{font-size:34px;font-weight:500;margin-bottom:22px}
.hero-features{list-style:none}
.hero-features li{display:flex;align-items:center;gap:12px;font-size:20px;height:36px}
.hero-features svg{flex:none}
.hero-actions{position:absolute;left:44px;top:322px;display:flex;gap:22px}
.btn-outline{width:163px;height:56px;border:3px solid var(--white);border-radius:28px;display:flex;align-items:center;justify-content:center;font-weight:700;font-size:18px;letter-spacing:.5px}
.store-badge{width:186px;height:56px;border-radius:8px;background:#000;border:2px solid #888}

.app-grid{position:absolute;left:53px;top:687px;width:1095px;display:grid;grid-template-columns:repeat(4,256px);column-gap:25px;row-gap:26px}
.app-tile{height:244px;background:var(--white);border:1px solid var(--line);box-shadow:0 2px 4px rgba(0,0,0,.15);padding:4px}
.app-art{height:172px}
.app-name{height:62px;display:flex;align-items:center;justify-content:center;font-size:22px;font-weight:500}
.app-tile.active{background:var(--accent-orange);border-color:var(--accent-orange)}
.app-tile.active .app-name{color:var(--white)}

.art-times{background:radial-gradient(ellipse 60px 90px at 10px 60px,#d8672c,rgba(216,103,44,0)),linear-gradient(180deg,var(--tile-navy) 0%,#2b4a6c 58%,#c9cfd6 78%,#b8bec5 100%)}
.art-ladybird{background:radial-gradient(ellipse 70px 50px at 150px 135px,#c8271f,rgba(200,39,31,0)),radial-gradient(ellipse 130px 70px at 110px 120px,#4f9a2a,rgba(79,154,42,0)),linear-gradient(180deg,#1f4a5e,#1d3b5c)}
.art-lines{background:radial-gradient(ellipse 80px 60px at 120px 80px,#8fa24a,rgba(143,162,74,0)),radial-gradient(ellipse 120px 40px at 120px 150px,#6a9a3c,rgba(106,154,60,0)),linear-gradient(180deg,#1e86d0,#1672b8)}
.art-place{background:radial-gradient(ellipse 50px 80px at 235px 80px,#d8672c,rgba(216,103,44,0)),linear-gradient(180deg,var(--tile-navy) 0%,var(--tile-navy) 50%,#dfe3e8 70%,#cdb08a 100%)}
.art-friends{background:radial-gradient(ellipse 50px 70px at 15px 40px,#d8672c,rgba(216,103,44,0)),radial-gradient(ellipse 100px 40px at 130px 130px,#f1d33a,rgba(241,211,58,0)),linear-gradient(180deg,var(--tile-navy) 0%,var(--tile-navy) 45%,#e9ecef 75%,#dde1e5 100%)}
.art-dominoes{background:radial-gradient(ellipse 50px 30px at 50px 20px,#3c9b3a,rgba(60,155,58,0)),radial-gradient(ellipse 100px 45px at 110px 120px,#f5f5f5,rgba(245,245,245,0)),linear-gradient(180deg,#1d3b5c,#22415f)}
.art-subitise{background:radial-gradient(ellipse 130px 40px at 130px 40px,#d8672c,rgba(216,103,44,0)),radial-gradient(ellipse 110px 40px at 130px 150px,#f1d33a,rgba(241,211,58,0)),linear-gradient(180deg,var(--tile-navy) 0%,var(--tile-navy) 55%,#eef0f2 75%,#eef0f2 100%)}
.art-add{background:radial-gradient(ellipse 40px 60px at 25px 30px,#d8672c,rgba(216,103,44,0)),radial-gradient(ellipse 100px 60px at 140px 90px,#f2f2f2,rgba(242,242,242,0)),linear-gradient(180deg,#1d3b5c,#1d3b5c)}
.art-sub{background:radial-gradient(ellipse 40px 60px at 25px 30px,#d8672c,rgba(216,103,44,0)),radial-gradient(ellipse 100px 65px at 130px 95px,#f2f2f2,rgba(242,242,242,0)),linear-gradient(180deg,#1d3b5c,#1d3b5c)}
.art-graphs{background:radial-gradient(ellipse 60px 60px at 190px 140px,#d8672c,rgba(216,103,44,0)),radial-gradient(ellipse 80px 50px at 100px 140px,#e39a32,rgba(227,154,50,0)),linear-gradient(180deg,#eceeef,#dde1e4)}
.art-missing{background:radial-gradient(ellipse 60px 110px at 130px 110px,#f2cfb4,rgba(242,207,180,0)),radial-gradient(ellipse 30px 40px at 35px 140px,#d8672c,rgba(216,103,44,0)),linear-gradient(180deg,#1d3b5c,#1d3b5c)}
.art-fraction{background:linear-gradient(180deg,#46607a 0%,#46607a 18%,#4aa93a 20%,#4aa93a 42%,#f0d83a 44%,#f0d83a 62%,#c02a26 64%,#c02a26 84%,#e0188a 86%,#e0188a 100%)}
.art-coords{background:radial-gradient(ellipse 80px 55px at 100px 150px,#d8672c,rgba(216,103,44,0)),linear-gradient(180deg,#4e6882,#3f5873)}
.art-mystery{background:radial-gradient(ellipse 120px 80px at 130px 85px,rgba(238,231,190,.75),rgba(238,231,190,0)),linear-gradient(180deg,#1d3b5c,#1d3b5c)}
.art-money{background:radial-gradient(ellipse 50px 45px at 110px 40px,#d8672c,rgba(216,103,44,0)),radial-gradient(ellipse 80px 40px at 80px 130px,#3a8a3a,rgba(58,138,58,0)),radial-gradient(ellipse 45px 35px at 200px 140px,#e4b43a,rgba(228,180,58,0)),linear-gradient(180deg,#f4f4f4,#ececec)}
.art-reading{background:radial-gradient(ellipse 70px 40px at 60px 70px,#f0cd2e,rgba(240,205,46,0)),radial-gradient(ellipse 60px 40px at 70px 160px,#d8672c,rgba(216,103,44,0)),linear-gradient(180deg,var(--tile-navy),#22415f)}

.site-footer{position:absolute;left:0;top:1848px;width:1200px;height:428px;background:var(--footer-navy);color:var(--white)}
.footer-mascot{position:absolute;left:88px;top:48px;width:262px;height:243px;border-radius:50% 50% 42% 42%;
  background:radial-gradient(ellipse 80px 70px at 131px 90px,#e4773a,rgba(228,119,58,0)),radial-gradient(ellipse 130px 120px at 131px 130px,#cf4d14,rgba(207,77,20,0) 100%);}
.footer-col{position:absolute;top:56px}
.footer-col h3{font-size:26px;font-weight:500;margin-bottom:18px}
.footer-col ul{list-style:none}
.footer-col li{font-size:19px;height:34px;padding-left:6px}
.col-main{left:466px}.col-social{left:740px}.col-curric{left:950px}
.footer-rule{position:absolute;left:53px;top:332px;width:1095px;height:1px;background:rgba(255,255,255,.3)}
.copyright{position:absolute;left:0;top:367px;width:1200px;text-align:center;font-size:19px}
.build-code{position:absolute;right:53px;top:364px;font-size:22px;font-weight:700}
</style>
</head>
<body>
<header class="site-header">
  <div class="brand"><span class="brand-dot"></span>Quiet Pebble Apps</div>
  <svg class="menu-toggle" width="34" height="30" viewBox="0 0 34 30"><g fill="#fff"><rect y="0" width="34" height="5"/><rect y="12" width="34" height="5"/><rect y="24" width="34" height="5"/></g></svg>
  <nav class="social-dots" aria-label="Social links">
    <span class="social-dot a"></span><span class="social-dot b"></span><span class="social-dot c"></span><span class="social-dot d"></span>
  </nav>
</header>

<section class="hero">
  <div class="hero-image" role="img" aria-label="Times tables game screens on a wooden desk with a gold medal and number picker"></div>
  <span class="hero-arrow prev"><svg width="16" height="24" viewBox="0 0 16 24"><path d="M13 3 4 12l9 9" stroke="#fff" stroke-width="3" fill="none"/></svg></span>
  <span class="hero-arrow next"><svg width="16" height="24" viewBox="0 0 16 24"><path d="M3 3l9 9-9 9" stroke="#fff" stroke-width="3" fill="none"/></svg></span>
  <div class="hero-panel">
    <h2 class="hero-title">Times Tables</h2>
    <ul class="hero-features">
      <li><svg width="17" height="17" viewBox="0 0 17 17"><circle cx="8.5" cy="8.5" r="8.5" fill="#fff"/><path d="M4.5 8.7l2.7 2.6 5.3-5.3" stroke="#d2531a" stroke-width="2.2" fill="none"/></svg>Multiplication to 12x12</li>
      <li><svg width="17" height="17" viewBox="0 0 17 17"><circle cx="8.5" cy="8.5" r="8.5" fill="#fff"/><path d="M4.5 8.7l2.7 2.6 5.3-5.3" stroke="#d2531a" stroke-width="2.2" fill="none"/></svg>Ability settings</li>
      <li><svg width="17" height="17" viewBox="0 0 17 17"><circle cx="8.5" cy="8.5" r="8.5" fill="#fff"/><path d="M4.5 8.7l2.7 2.6 5.3-5.3" stroke="#d2531a" stroke-width="2.2" fill="none"/></svg>Timed or untimed mode</li>
      <li><svg width="17" height="17" viewBox="0 0 17 17"><circle cx="8.5" cy="8.5" r="8.5" fill="#fff"/><path d="M4.5 8.7l2.7 2.6 5.3-5.3" stroke="#d2531a" stroke-width="2.2" fill="none"/></svg>Learn or testing mode</li>
      <li><svg width="17" height="17" viewBox="0 0 17 17"><circle cx="8.5" cy="8.5" r="8.5" fill="#fff"/><path d="M4.5 8.7l2.7 2.6 5.3-5.3" stroke="#d2531a" stroke-width="2.2" fill="none"/></svg>Compatible with tablets</li>
    </ul>
    <div class="hero-actions">
      <a class="btn-outline" href="#">MORE INFO</a>
      <span class="store-badge"></span>
    </div>
  </div>
</section>

<main class="app-grid">
  <a class="app-tile active" href="#"><div class="app-art art-times" role="img" aria-label="Times tables title over a number grid with monkey"></div><div class="app-name">Times Tables</div></a>
  <a class="app-tile" href="#"><div class="app-art art-ladybird" role="img" aria-label="Ladybird maths title with ladybird on a green leaf"></div><div class="app-name">Ladybird Maths</div></a>
  <a class="app-tile" href="#"><div class="app-art art-lines" role="img" aria-label="Frog on a lily pad above numbered stones"></div><div class="app-name">Number Lines</div></a>
  <a class="app-tile" href="#"><div class="app-art art-place" role="img" aria-label="Place value title with hundreds tens units blocks and monkey"></div><div class="app-name">Place Value MAB</div></a>
  <a class="app-tile" href="#"><div class="app-art art-friends" role="img" aria-label="Friends of ten title over a ten frame with counters"></div><div class="app-name">Friends Of Ten</div></a>
  <a class="app-tile" href="#"><div class="app-art art-dominoes" role="img" aria-label="Domino showing three and two with sum above"></div><div class="app-name">Dominoes Addition</div></a>
  <a class="app-tile" href="#"><div class="app-art art-subitise" role="img" aria-label="Subitising flash cards title over a card with yellow dots"></div><div class="app-name">Subitising Flash Cards</div></a>
  <a class="app-tile" href="#"><div class="app-art art-add" role="img" aria-label="Place value blocks addition on a board"></div><div class="app-name">Place Value MAB Add</div></a>
  <a class="app-tile" href="#"><div class="app-art art-sub" role="img" aria-label="Place value blocks subtraction on a board"></div><div class="app-name">Place Value MAB Sub</div></a>
  <a class="app-tile" href="#"><div class="app-art art-graphs" role="img" aria-label="Teaching graphs title over a bar chart with monkey"></div><div class="app-name">Teaching Graphs</div></a>
  <a class="app-tile" href="#"><div class="app-art art-missing" role="img" aria-label="Hand counting a missing number in a sum"></div><div class="app-name">Missing Numbers</div></a>
  <a class="app-tile" href="#"><div class="app-art art-fraction" role="img" aria-label="Coloured fraction wall of quarters thirds halves and a whole"></div><div class="app-name">Fraction Wall</div></a>
  <a class="app-tile" href="#"><div class="app-art art-coords" role="img" aria-label="Coordinate grid with plotted points and monkey"></div><div class="app-name">Coordinates</div></a>
  <a class="app-tile" href="#"><div class="app-art art-mystery" role="img" aria-label="Hundred chart with hidden numbers"></div><div class="app-name">Mystery Numbers</div></a>
  <a class="app-tile" href="#"><div class="app-art art-money" role="img" aria-label="Monkey with banknotes and coins"></div><div class="app-name">Teaching Money</div></a>
  <a class="app-tile" href="#"><div class="app-art art-reading" role="img" aria-label="Bananas with the word and numeral three and monkey"></div><div class="app-name">Reading Numbers</div></a>
</main>

<footer class="site-footer">
  <div class="footer-mascot" role="img" aria-label="Monkey mascot"></div>
  <div class="footer-col col-main"><h3>Main</h3><ul><li>Home</li><li>Support</li><li>Cookie policy</li><li>Volume purchasing</li><li>App privacy</li></ul></div>
  <div class="footer-col col-social"><h3>Social</h3><ul><li>Chirpline</li><li>Pinwall</li><li>Blog</li><li>Vidcast</li><li>IdeaBox</li><li>Friendlink</li></ul></div>
  <div class="footer-col col-curric"><h3>Curriculum</h3><ul><li>Australian</li><li>US Common Core</li><li>State Standards</li><li>UK School</li><li>New Zealand</li></ul></div>
  <div class="footer-rule"></div>
  <p class="copyright">© Quiet Pebble Apps 2018. All rights reserved.</p>
  <span class="build-code">C17</span>
</footer>
</body>
</html>
```